Brightwater Care Partners, LLC Business Card update!

would like a classier business card. Our cards currently just have our logo and contact information. Need better use of color and creativity
Logo attached.

Target Market(s)

Potential clients, contacts, existing clients. We are a consulting company

Industry/Entity Type

Business

Contact Information for Business Card

We like our colors but just have a boring card with our logo and a white background. I want something that stands out.

Colors
ec1f27
757575

Requirements
Must have
• Color to stay consistent. Logo provided
Nice to have
• Just better use of color/ design

```html
<!DOCTYPE html>
<html lang="en">
<head>
<meta charset="utf-8">
<title>Brightwater Care Partners – Business Card</title>
<link href="https://fonts.googleapis.com/css2?family=Source+Sans+3:wght@400;600&display=swap" rel="stylesheet">
<style>
  :root {
    --brand-red: #ec1f27;
    --brand-grey: #757575;
    --card-black: #0b0b0b;
    --accent-shape: #171717;
    --page-bg: #1c1c1c;
    --text-light: #e6e6e6;
    --text-white: #ffffff;
  }
  * { box-sizing: border-box; margin: 0; padding: 0; }
  html, body {
    width: 1200px;
    height: 900px;
    overflow: hidden;
    background: var(--page-bg);
    font-family: "Source Sans 3", "Myriad Pro", sans-serif;
  }
  .canvas {
    position: relative;
    width: 1200px;
    height: 900px;
    display: flex;
    align-items: center;
    justify-content: center;
  }
  .business-card {
    position: relative;
    width: 1000px;
    height: 572px;
    background: var(--card-black);
    box-shadow: 0 20px 50px rgba(0,0,0,0.6);
    overflow: hidden;
    padding: 64px 64px 0 0;
    display: flex;
    flex-direction: column;
    align-items: flex-end;
    text-align: right;
  }
  .background-emblem {
    position: absolute;
    left: 70px;
    top: 70px;
    width: 430px;
    height: 430px;
    border-radius: 50%;
    background: var(--accent-shape);
    z-index: 0;
  }
  .card-content {
    position: relative;
    z-index: 1;
    display: flex;
    flex-direction: column;
    align-items: flex-end;
  }
  .brand {
    display: flex;
    align-items: center;
    gap: 14px;
    margin-bottom: 48px;
  }
  .brand-mark {
    width: 30px;
    height: 30px;
    border-radius: 50%;
    background: var(--brand-grey);
  }
  .brand-name {
    font-weight: 600;
    font-size: 38px;
    line-height: 1.05;
    color: var(--brand-red);
    letter-spacing: 0.5px;
  }
  .owner-name {
    font-weight: 600;
    font-size: 30px;
    color: var(--text-white);
    line-height: 1.1;
  }
  .owner-title {
    font-weight: 400;
    font-size: 23px;
    color: var(--brand-red);
    margin-bottom: 34px;
  }
  .contact-list {
    list-style: none;
    display: flex;
    flex-direction: column;
    align-items: flex-end;
    gap: 6px;
  }
  .contact-item {
    display: flex;
    align-items: center;
    gap: 14px;
    font-size: 23px;
    color: var(--text-light);
  }
  .contact-icon {
    width: 18px;
    height: 18px;
    fill: var(--brand-red);
    stroke: var(--brand-red);
    flex: none;
  }
</style>
</head>
<body>
<main class="canvas">
  <section class="business-card" aria-label="Business card front">
    <div class="background-emblem" aria-hidden="true"></div>

    <div class="card-content">
      <div class="brand">
        <span class="brand-mark" aria-hidden="true"></span>
        <span class="brand-name">Brightwater Care Partners</span>
      </div>

      <p class="owner-name">Owner Name</p>
      <p class="owner-title">Managing Director</p>

      <ul class="contact-list">
        <li class="contact-item">
          <span>000 123 456 456</span>
          <svg class="contact-icon" viewBox="0 0 24 24" aria-hidden="true" stroke-width="0">
            <path d="M6.6 10.8a15 15 0 0 0 6.6 6.6l2.2-2.2a1 1 0 0 1 1-.25 11.4 11.4 0 0 0 3.6.57 1 1 0 0 1 1 1V20a1 1 0 0 1-1 1A17 17 0 0 1 3 4a1 1 0 0 1 1-1h3.5a1 1 0 0 1 1 1c0 1.25.2 2.45.57 3.6a1 1 0 0 1-.25 1z"/>
          </svg>
        </li>
        <li class="contact-item">
          <span>info@companyname.com</span>
          <svg class="contact-icon" viewBox="0 0 24 24" aria-hidden="true" stroke-width="0">
            <path d="M2 5h20v14H2z"/>
            <path d="M3 6.5l9 7 9-7" fill="none" stroke="#0b0b0b" stroke-width="1.8"/>
          </svg>
        </li>
        <li class="contact-item">
          <span>www.companyname.com</span>
          <svg class="contact-icon" viewBox="0 0 24 24" aria-hidden="true" fill="none" stroke-width="2.4" stroke-linecap="round">
            <path d="M10 14a4 4 0 0 0 5.7 0l3.6-3.6a4 4 0 0 0-5.7-5.7L12 6.3" fill="none"/>
            <path d="M14 10a4 4 0 0 0-5.7 0l-3.6 3.6a4 4 0 0 0 5.7 5.7L12 17.7" fill="none"/>
          </svg>
        </li>
        <li class="contact-item">
          <span>Address line1, Address Line, Country, 012</span>
          <svg class="contact-icon" viewBox="0 0 24 24" aria-hidden="true" stroke-width="0">
            <path d="M12 2a7 7 0 0 0-7 7c0 5 7 13 7 13s7-8 7-13a7 7 0 0 0-7-7zm0 9.5A2.5 2.5 0 1 1 12 6.5a2.5 2.5 0 0 1 0 5z"/>
          </svg>
        </li>
      </ul>
    </div>
  </section>
</main>
</body>
</html>
```